Young Architect Bussiness Card

English is not my first language (spanish is).
Need a bussiness card design for my best friend who is about to graduate from college, Licentiate degree in architecture, so she needs business cards to start networking, currently she has no porfolio, web page or plazared. so she is relying on her cel phone and correovela, but should leave space for one of them (plazared)

Design for business card should be modern, maybe something with construction blue prints patern or 3D modelling.

Name: Mariela Otárola Bonilla
Licentiate in Arquitecture
Cel: (506) XXX-4827
email: marielaXXX@correovela.com

Services, although im not sure if it has to be there or not:
Anteproyectos / Proposal design
Inspecciones / Site Inspections
Modelado 3D / 3D modelling
Planos Constructivos / Construction Blue Prints
Presupuestos / Budgets

Design should be in spanish

Industry/Entity Type

Architect

Contact Information for Business Card

Name: Mariela Otárola, Arquitecto
Associtation code : XXXX
Phone: (506) XXXX-XXXX
Email: xxx@correovela.com
Plazared: xxxx

Requirements
Must have
• Design for business card should be modern, maybe something with construction blue prints patern or 3D modelling.
Nice to have
• Something like a transition from 2D to 3D.

```html
<!DOCTYPE html>
<html lang="es">
<head>
<meta charset="utf-8">
<title>Mariela Otárola Bonilla — Tarjeta de presentación</title>
<link rel="stylesheet" href="https://fonts.googleapis.com/css2?family=Arimo:wght@400;700&display=swap">
<style>
  :root {
    --stage: #9a9a9a;
    --card-white: #f7f8f9;
    --navy: #1f3f7a;
    --red: #c81e1e;
    --grey-text: #6f7378;
    --blueprint: #173d74;
    --guide-light: #9fb2cf;
    --guide-dark: #4a6fa5;
    --white: #ffffff;
  }
  * { box-sizing: border-box; margin: 0; padding: 0; }
  html, body {
    width: 1073px;
    height: 1200px;
    overflow: hidden;
    background: var(--stage);
    font-family: "Arimo", Arial, sans-serif;
  }
  .card {
    position: absolute;
    left: 164px;
    width: 777px;
    height: 442px;
    overflow: hidden;
    box-shadow: 2px 3px 5px rgba(0, 0, 0, 0.35);
  }
  .card--front { top: 127px; background: var(--card-white); }
  .card--back { top: 639px; left: 166px; height: 440px; background: var(--blueprint); }

  .guides {
    position: absolute;
    inset: 0;
    width: 100%;
    height: 100%;
  }
  .guides--front line, .guides--front rect, .guides--front path { stroke: var(--guide-light); fill: none; stroke-width: 1.4; }
  .guides--back line, .guides--back rect, .guides--back path { stroke: var(--guide-dark); fill: none; stroke-width: 1.6; }
  .guides .dashed { stroke-dasharray: 14 6; }

  .front__drawing {
    position: absolute;
    left: 0; top: 55px;
    width: 100%; height: 300px;
    background: linear-gradient(180deg, rgba(201, 211, 226, 0) 0%, rgba(201, 211, 226, 0.35) 50%, rgba(201, 211, 226, 0) 100%);
  }
  .back__drawing {
    position: absolute;
    inset: 0;
    background: radial-gradient(ellipse at 50% 45%, #1e4680 0%, #173d74 60%, #143769 100%);
  }

  .front__identity {
    position: absolute;
    left: 0; right: 0; top: 139px;
    text-align: center;
  }
  .front__name {
    font-size: 38px;
    line-height: 44px;
    font-weight: 700;
    color: var(--navy);
    letter-spacing: 0.3px;
  }
  .front__title {
    font-size: 29px;
    line-height: 34px;
    font-weight: 700;
    color: var(--red);
  }
  .front__contact {
    position: absolute;
    left: 0; right: 0; top: 338px;
    text-align: center;
    font-size: 19px;
    line-height: 26px;
    color: var(--grey-text);
  }
  .front__contact .label { color: var(--navy); }

  .services {
    position: absolute;
    left: 0; right: 0; top: 145px;
    list-style: none;
    text-align: center;
    font-size: 25px;
    font-weight: 700;
    line-height: 33px;
    color: var(--white);
    text-shadow: 1px 1px 0 #8a1717, -1px -1px 0 #8a1717, 1px -1px 0 #8a1717, -1px 1px 0 #8a1717;
  }
  .services .service--highlight {
    color: var(--red);
    text-shadow: 1px 1px 0 #f1d6d6, -1px -1px 0 #f1d6d6, 1px -1px 0 #f1d6d6, -1px 1px 0 #f1d6d6;
  }
</style>
</head>
<body>
  <section class="card card--front" aria-label="Frente de la tarjeta">
    <div class="front__drawing" role="img" aria-label="Plano arquitectónico tenue de la cercha de un techo"></div>
    <svg class="guides guides--front" viewBox="0 0 777 442" aria-hidden="true">
      <line class="dashed" x1="0" y1="25" x2="777" y2="25"/>
      <line class="dashed" x1="0" y1="88" x2="300" y2="88"/>
      <line class="dashed" x1="480" y1="88" x2="777" y2="88"/>
      <line class="dashed" x1="0" y1="288" x2="777" y2="288"/>
      <line x1="60" y1="0" x2="60" y2="442"/>
      <line x1="717" y1="0" x2="717" y2="442"/>
      <line x1="388" y1="0" x2="388" y2="120"/>
      <line x1="0" y1="250" x2="777" y2="250"/>
      <line x1="0" y1="262" x2="777" y2="262"/>
      <rect x="20" y="0" width="737" height="442"/>
    </svg>
    <header class="front__identity">
      <h1 class="front__name">Mariela Otárola Bonilla</h1>
      <p class="front__title">Licentiate in Arquitecture</p>
    </header>
    <div class="front__contact">
      <p><span class="label">e-mail:</span> marielaXXX@correovela.com | <span class="label">mobil:</span>&nbsp; (506) XXX-4827</p>
      <p><span class="label">plazared:</span> marielaXXX</p>
    </div>
  </section>

  <section class="card card--back" aria-label="Reverso de la tarjeta">
    <div class="back__drawing" role="img" aria-label="Plano arquitectónico tenue de una planta en líneas claras sobre azul"></div>
    <svg class="guides guides--back" viewBox="0 0 777 440" aria-hidden="true">
      <line x1="0" y1="30" x2="777" y2="30"/>
      <line x1="0" y1="410" x2="777" y2="410"/>
      <line x1="0" y1="380" x2="777" y2="380"/>
      <line x1="70" y1="0" x2="70" y2="440"/>
      <line x1="150" y1="0" x2="150" y2="440"/>
      <line x1="640" y1="0" x2="640" y2="440"/>
      <line x1="700" y1="0" x2="700" y2="440"/>
      <line class="dashed" x1="0" y1="100" x2="777" y2="100"/>
      <line class="dashed" x1="0" y1="320" x2="777" y2="320"/>
      <line class="dashed" x1="388" y1="0" x2="388" y2="440"/>
      <rect x="180" y="60" width="420" height="320"/>
    </svg>
    <ul class="services">
      <li>Anteproyectos / Proposal design</li>
      <li>Inspecciones / Site Inspections</li>
      <li class="service--highlight">Modelado 3D / 3D modelling</li>
      <li>Planos Constructivos / Construction Blue Prints</li>
      <li>Presupuestos / Budgets</li>
    </ul>
  </section>
</body>
</html>
```